New Innovative Counselling and psychotherapy Service needs Business Card design

Keep it simple and professional. On one side, just company name and logo (perhaps in all blue) and maybe a tag line.

On other side (all white) my name and Qualifications in centre

Industry/Entity Type

Health And Wellness

Contact Information for Business Card

Dara Whelby
Counsellor & Psychotherapist
BSc (Psychol.), BA, Dip. (Couns. & Psych.), PG.Cert (CBT), FGTrK, ONRE

I will also require Mobile no, Email and web site address of which I'll pass on to final designer.

Font styles to use
Sans Serif

Requirements
Must have
• My Logo Only and please use the colours in logo that is in it.
Should not have
• Any other images

```html
<!DOCTYPE html>
<html lang="en">
<head>
<meta charset="utf-8">
<title>Thrive Lane – Business Card</title>
<link href="https://fonts.googleapis.com/css2?family=Roboto:wght@300;400;700&display=swap" rel="stylesheet">
<style>
  :root {
    --backdrop: #3a3a3c;
    --card: #1f2022;
    --card-edge: #151617;
    --emboss: #4a4b4e;
    --brand-blue: #3fb0ea;
    --brand-green: #8cc63f;
    --text-light: #f2f2f2;
  }
  * { margin: 0; padding: 0; box-sizing: border-box; }
  html, body {
    width: 799px; height: 1200px; overflow: hidden;
    background: var(--backdrop);
    font-family: "Roboto", Arial, sans-serif;
  }
  .canvas {
    position: relative; width: 799px; height: 1200px;
  }
  .card {
    position: absolute; left: 80px; width: 640px; height: 366px;
    background: var(--card);
    border-radius: 26px;
    box-shadow: 0 3px 0 var(--card-edge), 0 14px 30px rgba(0,0,0,.45);
  }
  .card--front { top: 150px; }
  .card--back  { top: 684px; }

  .front-brand {
    position: absolute; inset: 0;
    display: flex; align-items: center; justify-content: center; gap: 18px;
  }
  .front-brand__dot {
    width: 54px; height: 54px; border-radius: 50%;
    background: var(--emboss);
  }
  .front-brand__name {
    font-size: 44px; font-weight: 300; color: var(--emboss); letter-spacing: .5px;
  }

  .back-brand {
    position: absolute; left: 48px; top: 96px; width: 240px;
    display: flex; flex-direction: column; align-items: center; gap: 18px;
  }
  .back-brand__dot {
    width: 104px; height: 104px; border-radius: 50%;
    background: var(--brand-blue);
  }
  .back-brand__name {
    font-size: 34px; font-weight: 300; color: var(--text-light); white-space: nowrap;
  }

  .contact {
    position: absolute; left: 330px; top: 96px; width: 290px;
    color: var(--text-light);
  }
  .contact__name {
    font-size: 26px; font-weight: 700; color: var(--brand-blue); line-height: 1.1;
  }
  .contact__role, .contact__quals {
    font-size: 13px; font-weight: 400; line-height: 1.35;
  }
  .contact__list {
    list-style: none; margin-top: 22px;
  }
  .contact__item {
    display: flex; align-items: center; gap: 12px;
    font-size: 15px; line-height: 1.6;
  }
  .contact__icon { width: 14px; height: 14px; flex: none; }
</style>
</head>
<body>
<main class="canvas">
  <section class="card card--front" aria-label="Card front">
    <div class="front-brand">
      <span class="front-brand__dot"></span>
      <span class="front-brand__name">Thrive Lane</span>
    </div>
  </section>

  <section class="card card--back" aria-label="Card back">
    <div class="back-brand">
      <span class="back-brand__dot"></span>
      <span class="back-brand__name">Thrive Lane</span>
    </div>

    <div class="contact">
      <h1 class="contact__name">Dara Whelby</h1>
      <p class="contact__role">Counsellor &amp; Psychotherapist</p>
      <p class="contact__quals">BSc (Psychol.), BA, Dip. (Couns. &amp; Psych.),<br>PG.Cert (CBT), FGTrK, ONRE</p>

      <ul class="contact__list">
        <li class="contact__item">
          <svg class="contact__icon" viewBox="0 0 14 14"><path fill="#3fb0a0" d="M3 1h2l1 3-1.5 1a8 8 0 0 0 4.5 4.5L10 8l3 1v2c0 1-1 2-2 2A10 10 0 0 1 1 3c0-1 1-2 2-2z"/></svg>
          <span>0100 555 0142</span>
        </li>
        <li class="contact__item">
          <svg class="contact__icon" viewBox="0 0 14 14"><rect x="1" y="3" width="12" height="8" rx="1" fill="#8cc63f"/><path d="M1.5 3.5 7 8l5.5-4.5" stroke="#1f2022" stroke-width="1.2" fill="none"/></svg>
          <span>dara.w@ThriveLane.com</span>
        </li>
        <li class="contact__item">
          <svg class="contact__icon" viewBox="0 0 14 14"><circle cx="7" cy="7" r="6" fill="#3fb0ea"/><path d="M1 7h12M7 1c-3 3-3 9 0 12M7 1c3 3 3 9 0 12" stroke="#1f2022" stroke-width="1" fill="none"/></svg>
          <span>www.ThriveLane.com</span>
        </li>
      </ul>
    </div>
  </section>
</main>
</body>
</html>
```